Veldmark Supplies Business Card

Professional business card that stand out to our potential customers. Front and back with clean modern design

Industry/Entity Type

Oil and gas

Contact Information for Business Card

Name, address, website , office phone and cell number

Requirements
Must have
• Editable files for each employee

```html
<!DOCTYPE html>
<html lang="en">
<head>
<meta charset="utf-8">
<title>Veldmark Supplies Business Card</title>
<link href="https://fonts.googleapis.com/css2?family=Poppins:wght@400;500;700&display=swap" rel="stylesheet">
<style>
  :root {
    --red: #e8202a;
    --blue: #1eaacb;
    --ink: #1c1c1c;
    --card-white: #ffffff;
    --card-black: #111111;
    --stage: #2a2a2a;
  }
  * { margin: 0; padding: 0; box-sizing: border-box; }
  html, body { width: 1200px; height: 900px; overflow: hidden; }
  body {
    background: var(--stage);
    font-family: "Poppins", sans-serif;
    position: relative;
  }
  .card {
    position: absolute;
    width: 600px;
    height: 343px;
    border-radius: 22px;
    overflow: hidden;
  }
  /* Back of card */
  .card-back {
    left: 300px;
    top: 60px;
    background: var(--card-black);
  }
  .back-pattern {
    position: absolute;
    inset: 0;
    background: linear-gradient(120deg, #6d6d6d 0%, #3a3a3a 40%, #161616 75%, #0c0c0c 100%);
  }
  .back-brand {
    position: absolute;
    right: 70px;
    bottom: 80px;
    display: flex;
    align-items: center;
    gap: 8px;
    background: var(--card-black);
    padding: 8px 12px;
    border-radius: 6px;
  }
  .brand-square {
    width: 14px;
    height: 14px;
    background: var(--red);
  }
  .back-brand .brand-name {
    color: var(--red);
    font-weight: 700;
    font-size: 18px;
  }
  /* Front of card */
  .card-front {
    left: 300px;
    top: 480px;
    background: var(--card-white);
  }
  .front-brand {
    position: absolute;
    left: 36px;
    top: 40px;
    display: flex;
    align-items: center;
    gap: 12px;
  }
  .front-brand .brand-square { width: 26px; height: 26px; }
  .front-brand .brand-name {
    color: var(--red);
    font-weight: 700;
    font-size: 34px;
    letter-spacing: 1px;
    text-transform: uppercase;
  }
  .person {
    position: absolute;
    left: 52px;
    top: 132px;
  }
  .person-name {
    color: var(--red);
    font-weight: 700;
    font-size: 27px;
    line-height: 1.1;
  }
  .person-title {
    color: var(--ink);
    font-size: 15px;
    margin-top: 2px;
  }
  .name-rule {
    position: absolute;
    left: 52px;
    right: 56px;
    top: 197px;
    height: 1px;
    background: var(--red);
  }
  .contacts {
    position: absolute;
    left: 52px;
    top: 208px;
    list-style: none;
    font-size: 15px;
    color: var(--ink);
    line-height: 21px;
  }
  .contacts li { display: flex; align-items: center; gap: 8px; }
  .contacts svg { width: 12px; height: 12px; fill: var(--red); flex: none; }
  .address {
    position: absolute;
    right: 40px;
    top: 210px;
    font-size: 15px;
    line-height: 20px;
    color: var(--ink);
  }
  .bottom-band {
    position: absolute;
    left: 0;
    bottom: 0;
    width: 600px;
    height: 14px;
  }
</style>
</head>
<body>

<section class="card card-back" aria-label="Card back">
  <div class="back-pattern" role="img" aria-label="Repeating monogram pattern on black, fading from grey to black"></div>
  <div class="back-brand">
    <span class="brand-square"></span>
    <span class="brand-name">Veldmark Supplies</span>
  </div>
</section>

<section class="card card-front" aria-label="Card front">
  <div class="front-brand">
    <span class="brand-square"></span>
    <span class="brand-name">Veldmark Supplies</span>
  </div>

  <div class="person">
    <div class="person-name">Corin Halvey</div>
    <div class="person-title">President</div>
  </div>
  <div class="name-rule"></div>

  <ul class="contacts">
    <li><svg viewBox="0 0 12 12"><path d="M1 3c0-1 1-2 2-2h6c1 0 2 1 2 2v1H8V3H4v1H1z M2 5h8l1 6H1z"/></svg>(555)014-2290</li>
    <li><svg viewBox="0 0 12 12"><path d="M3 0h6v12H3z M4 1v8h4V1z"/></svg>(555)014-2290</li>
    <li><svg viewBox="0 0 12 12"><path d="M0 2h12v8H0z M0 2l6 4 6-4" stroke="#fff" stroke-width="1"/></svg>sales@veldmarksupplies.com</li>
    <li><svg viewBox="0 0 12 12"><circle cx="6" cy="6" r="6"/></svg>www.veldmarksupplies.com</li>
  </ul>

  <div class="address">412 N.Birchline Suite 5<br>Marlow, Tx 79012</div>

  <svg class="bottom-band" viewBox="0 0 600 14" preserveAspectRatio="none" aria-hidden="true">
    <polygon points="0,0 400,0 390,14 0,14" fill="var(--red)"/>
    <polygon points="400,0 600,0 600,14 390,14" fill="var(--blue)"/>
  </svg>
</section>

</body>
</html>
```